Woman owned consulting company needs an elegant and modern business card design

I need a business card design for my new consulting company, Mara Quillon Consulting. I am looking for something that is simple and elegant, but also creative and original. You can use either version of the logo that are attached. I have also included the information that needs to be featured on the business card.

Contact Information for Business Card

Requirements
Must have
• The logo and the font type and a standard business card size. Use shades of gray/silver and or rose gold that are in the logo.
• I didn't realize that my actual logo wasn't attached. Please incorporate in the designs.
Should not have
• Colors that are different from my logo

```html
<!DOCTYPE html>
<html lang="en">
<head>
<meta charset="utf-8">
<title>Mara Quillon Consulting — Business Card</title>
<link href="https://fonts.googleapis.com/css2?family=Cormorant+Garamond:wght@400;500&display=swap" rel="stylesheet">
<style>
  :root {
    --backdrop: #2b2c2e;
    --card-black: #111213;
    --card-slate: #3b3f42;
    --emboss: #2a2b2d;
    --silver: #cfd2d4;
    --silver-soft: #9a9ea1;
    --text-light: #e4e6e7;
    --text-muted: #b3b7ba;
  }
  * { margin: 0; padding: 0; box-sizing: border-box; }
  html, body { width: 800px; height: 1200px; overflow: hidden; }
  body {
    background: var(--backdrop);
    font-family: "Cormorant Garamond", Georgia, serif;
    position: relative;
  }
  .card {
    position: absolute;
    left: 80px;
    width: 640px;
    height: 366px;
    box-shadow: 0 18px 40px rgba(0,0,0,0.45);
    overflow: hidden;
  }
  .card--front { top: 150px; background: var(--card-black); }
  .card--back { top: 690px; background: var(--card-slate); }

  .front-wordmark {
    position: absolute;
    inset: 0;
    display: flex;
    align-items: center;
    justify-content: center;
    font-size: 46px;
    font-weight: 400;
    letter-spacing: 1px;
    color: var(--emboss);
  }

  .back-art { position: absolute; inset: 0; }

  .holder { position: absolute; left: 38px; top: 46px; }
  .holder-name {
    font-size: 19px;
    font-weight: 500;
    letter-spacing: 2px;
    color: var(--text-light);
  }
  .holder-title {
    font-size: 14px;
    color: var(--text-muted);
    margin-top: 2px;
  }

  .contacts {
    position: absolute;
    left: 38px;
    top: 226px;
    list-style: none;
  }
  .contact {
    display: flex;
    align-items: center;
    gap: 10px;
    font-size: 14px;
    color: var(--text-muted);
    margin-bottom: 9px;
  }
  .contact svg { width: 14px; height: 14px; flex: none; }

  .back-wordmark {
    position: absolute;
    left: 420px;
    right: 20px;
    top: 0;
    bottom: 0;
    display: flex;
    flex-direction: column;
    align-items: center;
    justify-content: center;
    font-size: 34px;
    font-weight: 400;
    line-height: 1.05;
    color: var(--silver);
    text-align: center;
  }
</style>
</head>
<body>
  <section class="card card--front" aria-label="Card front">
    <div class="front-wordmark">Mara Quillon Consulting</div>
  </section>

  <section class="card card--back" aria-label="Card back">
    <svg class="back-art" viewBox="0 0 640 366" width="640" height="366" aria-hidden="true">
      <path d="M372 0 Q300 183 372 366" fill="none" stroke="var(--silver-soft)" stroke-width="3"/>
      <path d="M392 0 Q320 183 392 366 L640 366 L640 0 Z" fill="var(--card-black)"/>
    </svg>

    <div class="holder">
      <div class="holder-name">MARA QUILLON</div>
      <div class="holder-title">Owner</div>
    </div>

    <ul class="contacts">
      <li class="contact">
        <svg viewBox="0 0 16 16"><path d="M4 1.5 L6.5 4.5 L5 6.5 Q6.5 9.5 9.5 11 L11.5 9.5 L14.5 12 L12.5 14.5 Q5 13 1.5 3.5 Z" fill="var(--text-muted)"/></svg>
        (555) 014-2290
      </li>
      <li class="contact">
        <svg viewBox="0 0 16 16"><rect x="1.5" y="3.5" width="13" height="9" fill="none" stroke="var(--text-muted)" stroke-width="1.4"/><path d="M1.5 3.5 L8 9 L14.5 3.5" fill="none" stroke="var(--text-muted)" stroke-width="1.4"/></svg>
        mara@maraquillon.com
      </li>
      <li class="contact">
        <svg viewBox="0 0 16 16"><circle cx="8" cy="8" r="6.3" fill="none" stroke="var(--text-muted)" stroke-width="1.3"/><ellipse cx="8" cy="8" rx="2.8" ry="6.3" fill="none" stroke="var(--text-muted)" stroke-width="1.1"/><path d="M1.7 8 H14.3" stroke="var(--text-muted)" stroke-width="1.1"/></svg>
        www.maraquillon.com
      </li>
    </ul>

    <div class="back-wordmark">
      <span>Mara Quillon</span>
      <span>Consulting</span>
    </div>
  </section>
</body>
</html>
```